A start-up named "Corvane Therapeutics" - needs a new PowerPoint design

We need a new PowerPoint Design for an early-stage start-up named "Corvane Therapeutics" seeking to disrupt the current approach towards drug discovery within aging disorders.

We would like to build on Corvane's legacy, the founder of the modern science of genetics, by employing a multidisciplinary approach, experimenting, and providing elderly patients the attention they deserve.

We have selected the suffix "therapeutics" intentionally as it stands for (a medicine) the treatment of disease; the science of healing. Alzheimer’s treatment is a huge, urgent, unmet need:
- Shift from a disease-management system to a preventive medicine system
- Focus on increasing the health span, not only the life span

Target Market(s)

Pharma/ Biotech Executives Medical Institutions Healthcare professionals (MDs, nurses, payors, pharmacists, etc.) Patients

Industry/Entity Type

Healthcare

Other font styles liked:
• Celias

Colors
0054AA
0677BA
7BADD7
CADEEF
E8F1F8
E54698
E96AAD
F1A4CE
F9D9EA
FCEFF6
A7469A
B969AE
D3A5CF
EDDBEB
F8F0F9
6B429C
8869AF
B7A5CE
E3DAEB
F3F0F8

Requirements
Must have
• - differentiate from other companies named after Corvane - differentiate from other Pharma/ Biotech companies
Nice to have
• simplicity/ minimalist logo vivid colors gradient 3D Life-Sciences inspired Simple geometry Balance
Should not have
• mascot/ emblem watermark logo animated ink style nature-inspired inventive typography artistic chaos

```html
<!DOCTYPE html>
<html lang="en">
<head>
<meta charset="utf-8">
<title>Corvane Therapeutics – Presentation Template, Part 2</title>
<link rel="stylesheet" href="https://fonts.googleapis.com/css2?family=Arimo:wght@400;700&display=swap">
<style>
  :root{
    --blue-900:#0054AA;
    --blue-700:#0677BA;
    --blue-400:#7BADD7;
    --blue-100:#CADEEF;
    --pink-600:#E54698;
    --pink-500:#E96AAD;
    --magenta-600:#A7469A;
    --purple-700:#6B429C;
    --purple-band:#622D8F;
    --ink:#1a1a1a;
    --grid:#d9d9d9;
    --white:#ffffff;
  }
  *{box-sizing:border-box;margin:0;padding:0}
  html,body{width:1200px;height:1200px;overflow:hidden;background:var(--white)}
  body{position:relative;font-family:"Arimo",Arial,sans-serif;color:var(--ink)}

  .slide{position:absolute;width:517px;overflow:hidden}
  .slide--content{top:40px;height:292px;background:var(--white)}
  .slide--charts{left:61.5px}
  .slide--team{left:618.5px}

  .slide-title{position:absolute;left:16px;top:21px;font-size:16.5px;font-weight:700;color:var(--blue-900)}
  .corner-mark{position:absolute;right:16px;top:21px;font-size:9px;font-weight:700;color:var(--blue-900);display:flex;align-items:center;gap:4px}
  .corner-mark i{display:block;width:10px;height:10px;background:var(--blue-900)}

  .slide-footer{position:absolute;left:0;bottom:0;width:100%;height:21.5px;
    background:linear-gradient(90deg,var(--pink-500) 0%,var(--pink-600) 35%,var(--magenta-600) 70%,var(--purple-700) 100%);
    color:var(--white);font-size:5.3px;display:flex;align-items:center;justify-content:space-between;padding:0 18px 0 16px}
  .slide-footer b{font-weight:700;font-size:5.6px}

  .charts-svg{position:absolute;left:0;top:0}
  .chart-note{position:absolute;left:275px;top:223px;width:230px;font-size:7.4px;line-height:1.25}

  .section-header{position:absolute;left:16px;top:55px;font-size:8.4px;font-weight:700;color:var(--pink-600)}
  .section-copy{position:absolute;left:16px;top:67px;width:486px;font-size:7.3px;line-height:1.22}
  .member{position:absolute;top:96.5px;width:148px}
  .member--one{left:16px}
  .member--two{left:184.5px}
  .member--three{left:353px}
  .member__photo{height:130.5px}
  .member--one .member__photo{background:linear-gradient(160deg,#6f8f3a,#a9b66a 45%,#e6e0d6)}
  .member--two .member__photo{background:linear-gradient(170deg,#e4e6ea,#b9c2cf 55%,#5b7fa8)}
  .member--three .member__photo{background:linear-gradient(170deg,#d6d9de,#8a96b8 50%,#4f6fc2)}
  .member__name{margin-top:5px;height:22.5px;background:linear-gradient(90deg,#5aa0d6,var(--blue-900));
    color:var(--white);font-size:10px;font-weight:700;display:flex;align-items:center;justify-content:center}

  .slide--cover{top:367px;height:291px}
  .slide--break{left:61.5px;background:linear-gradient(100deg,#d9569e 0%,#c46bb6 40%,#9d5aa8 75%,#7d4a9e 100%)}
  .slide--thanks{left:618.5px;background:linear-gradient(100deg,#6aa6d8 0%,#3f8acb 40%,#1a6dbd 75%,#0b5bb0 100%)}
  .cover-brand{position:absolute;left:22px;top:30px;color:var(--white);font-weight:400;line-height:1}
  .cover-brand span{display:block;font-size:20px}
  .cover-brand small{display:block;font-size:9.4px;letter-spacing:1.2px;margin-top:1px}
  .cover-title{position:absolute;left:21px;top:104px;font-size:47px;font-weight:700;color:var(--white);letter-spacing:.3px}
  .cover-rule{position:absolute;left:21px;top:166px;width:35px;height:2.2px;background:var(--white)}
  .cover-copy{position:absolute;left:21px;top:182px;width:470px;font-size:8px;line-height:1.3;color:var(--white)}

  .part-band{position:absolute;left:0;top:1037px;width:1200px;height:127px;background:var(--purple-band)}
  .part-band h1{position:absolute;left:62px;top:18px;font-size:76px;font-weight:700;color:var(--white);letter-spacing:1px}
</style>
</head>
<body>

<section class="slide slide--content slide--charts">
  <h2 class="slide-title">Data Chart Analysis</h2>
  <div class="corner-mark"><i></i>Corvane</div>

  <svg class="charts-svg" width="517" height="270" viewBox="0 0 517 270" font-family="Arimo, Arial, sans-serif">
    <text x="126" y="68" font-size="8.6" font-weight="700" fill="#E54698" text-anchor="middle">Chart Title</text>
    <g transform="translate(126 157.5) rotate(-90)" fill="none" stroke-width="19.8">
      <circle r="70.8" stroke="#0054AA" stroke-dasharray="260.7 444.9"/>
      <circle r="70.8" stroke="#0677BA" stroke-dasharray="101.9 444.9" stroke-dashoffset="-260.7"/>
      <circle r="70.8" stroke="#7BADD7" stroke-dasharray="44.5 444.9" stroke-dashoffset="-362.6"/>
      <circle r="70.8" stroke="#E54698" stroke-dasharray="37.8 444.9" stroke-dashoffset="-407.1"/>
      <circle r="70.8" stroke="#ffffff" stroke-width="20" stroke-dasharray="1 259.7 1 100.9 1 43.5 1 36.8"/>
    </g>
    <g font-size="6" fill="#333">
      <rect x="69" y="246" width="3" height="3" fill="#0054AA"/><text x="74" y="249.5">1st Qtr</text>
      <rect x="99" y="246" width="3" height="3" fill="#0677BA"/><text x="104" y="249.5">2nd Qtr</text>
      <rect x="131" y="246" width="3" height="3" fill="#7BADD7"/><text x="136" y="249.5">3rd Qtr</text>
      <rect x="162" y="246" width="3" height="3" fill="#E54698"/><text x="167" y="249.5">4th Qtr</text>
    </g>

    <line x1="258.5" y1="59" x2="258.5" y2="258" stroke="#e3e3e3" stroke-width=".8"/>

    <text x="387.5" y="68" font-size="8.6" font-weight="700" fill="#E54698" text-anchor="middle">Chart Title</text>
    <g stroke="#d9d9d9" stroke-width=".6">
      <line x1="315.5" y1="75" x2="315.5" y2="185"/>
      <line x1="351" y1="75" x2="351" y2="185"/>
      <line x1="386.5" y1="75" x2="386.5" y2="185"/>
      <line x1="422" y1="75" x2="422" y2="185"/>
      <line x1="457.5" y1="75" x2="457.5" y2="185"/>
      <line x1="493" y1="75" x2="493" y2="185"/>
    </g>
    <g fill="#0677BA">
      <rect x="315.5" y="80" width="99.4" height="8"/>
      <rect x="315.5" y="107.5" width="63.9" height="8"/>
      <rect x="315.5" y="135" width="156.2" height="8"/>
      <rect x="315.5" y="162" width="85.2" height="8"/>
    </g>
    <g fill="#E54698">
      <rect x="315.5" y="92" width="159.8" height="8"/>
      <rect x="315.5" y="119.5" width="124.3" height="8"/>
      <rect x="315.5" y="147" width="88.8" height="8"/>
      <rect x="315.5" y="174" width="152.7" height="8"/>
    </g>
    <g font-size="6.4" fill="#333" text-anchor="end">
      <text x="310" y="92">Category 4</text>
      <text x="310" y="119.5">Category 3</text>
      <text x="310" y="147">Category 2</text>
      <text x="310" y="174.5">Category 1</text>
    </g>
    <g font-size="6.4" fill="#333" text-anchor="middle">
      <text x="315.5" y="196">0</text><text x="351" y="196">1</text><text x="386.5" y="196">2</text>
      <text x="422" y="196">3</text><text x="457.5" y="196">4</text><text x="493" y="196">5</text>
    </g>
    <g font-size="6.4" fill="#333">
      <rect x="357" y="203.5" width="3" height="3" fill="#0677BA"/><text x="362" y="207">Series 2</text>
      <rect x="391" y="203.5" width="3" height="3" fill="#E54698"/><text x="396" y="207">Series 1</text>
    </g>
  </svg>

  <p class="chart-note">Lorem ipsum dolor sit amet, consectetur adipiscing elit. Curabitur at fringilla velit. In ac sagittis nulla. Nulla quis erat et ligula aliquam sagittis in viverra mauris. Pellentesque pharetra hendrerit orci at.</p>

  <footer class="slide-footer"><span>Copywrite Statement 2022</span><b>5</b></footer>
</section>

<section class="slide slide--content slide--team">
  <h2 class="slide-title">Meet Our Team</h2>
  <div class="corner-mark"><i></i>Corvane</div>
  <h3 class="section-header">Section Header</h3>
  <p class="section-copy">Donec vel suscipit purus, ultrices ornare neque. Sed nec est a lacus lacinia venenatis non at est. Vestibulum vitae lorem lectus. Phasellus gravida mauris a sapien elementum malesuada. Vestibulum ut urna eu dolor.</p>

  <div class="member member--one">
    <div class="member__photo" role="img" aria-label="Portrait photo of a team member outdoors in front of trees"></div>
    <div class="member__name">Enter Name Here</div>
  </div>
  <div class="member member--two">
    <div class="member__photo" role="img" aria-label="Portrait photo of a team member in a white lab coat"></div>
    <div class="member__name">Enter Name Here</div>
  </div>
  <div class="member member--three">
    <div class="member__photo" role="img" aria-label="Portrait photo of a team member in blue scrubs with a stethoscope"></div>
    <div class="member__name">Enter Name Here</div>
  </div>

  <footer class="slide-footer"><span>Copywrite Statement 2022</span><b>6</b></footer>
</section>

<section class="slide slide--cover slide--break" role="img" aria-label="Pink-tinted photo of a scientist pipetting samples into a tube rack">
  <div class="cover-brand"><span>Corvane</span><small>Therapeutics</small></div>
  <h2 class="cover-title">Break Slide</h2>
  <div class="cover-rule"></div>
  <p class="cover-copy">Donec vel suscipit purus, ultrices ornare neque. Sed nec est a lacus lacinia venenatis non at est. Vestibulum vitae lorem lectus. Phasellus gravida mauris a sapien elementum malesuada. Vestibulum ut urna eu dolor.</p>
</section>

<section class="slide slide--cover slide--thanks" role="img" aria-label="Blue-tinted photo of a scientist pipetting samples into a tube rack">
  <div class="cover-brand"><span>Corvane</span><small>Therapeutics</small></div>
  <h2 class="cover-title">Thank You!</h2>
  <div class="cover-rule"></div>
  <p class="cover-copy">Donec vel suscipit purus, ultrices ornare neque. Sed nec est a lacus lacinia venenatis non at est. Vestibulum vitae lorem lectus. Phasellus gravida mauris a sapien elementum malesuada. Vestibulum ut urna eu dolor.</p>
</section>

<div class="part-band"><h1>PART 2</h1></div>

</body>
</html>
```